Unternehmen für Ordnung und Sauberkeit am Arbeitsplatz und Produkte zur Produktionsoptimierung benötigt Visitenkarten und Briefpapier
Zielgruppe
Produkte für Ordnung und Sauberkeit am Arbeitsplatz, Organisation von Arbeitsplätzen, Produkte zur Vereinfachung von Arbeitsabläufen, Produkte zur Produktionsoptimierung unter dem Lean Gedanke, Schlagwort: "5S", nachhaltig, sauber
Aufgabenstellung
Wir sind auf der Suche nach Visitenkarten und Briefpapier für das Unternehmen yourTidor. Nachhaltig, Sauber usw.. Unser Firmenlogo finden Sie anbei.

```html
<!DOCTYPE html>
<html lang="de">
<head>
<meta charset="utf-8">
<title>yourTidor – Briefpapier und Umschlag</title>
<link rel="stylesheet" href="https://fonts.googleapis.com/css2?family=Source+Sans+3:wght@400;700&display=swap">
<style>
  :root {
    --green: #2aaa37;
    --green-dark: #1e7d2b;
    --grey: #848484;
    --grey-text: #8a8a8a;
    --paper: #ffffff;
    --mark: #6b6b6b;
    --faint: #f4f4f4;
  }
  html, body { margin: 0; padding: 0; overflow: hidden; }
  body { width: 1200px; height: 1000px; background: var(--paper); position: relative; font-family: "Source Sans 3", sans-serif; }
  .artboard { position: absolute; inset: 0; }
  .sheet { position: absolute; background: var(--paper); box-shadow: 3px 3px 4px rgba(0,0,0,0.22); }
  .letterhead { left: 96px; top: 202px; width: 420px; height: 595px; }
  .envelope-front { left: 653px; top: 254px; width: 450px; height: 231px; }
  .envelope-back { left: 653px; top: 566px; width: 450px; height: 231px; }
  .guides { position: absolute; inset: 0; pointer-events: none; }
  .abs { position: absolute; }
  .brand { font-weight: 700; color: var(--green-dark); white-space: nowrap; line-height: 1; }
  .brand-mark { display: inline-block; background: var(--green); border-radius: 3px; vertical-align: middle; }
  .logo-main { left: 36px; top: 28px; font-size: 38px; display: flex; align-items: center; gap: 8px; }
  .logo-main .brand-mark { width: 26px; height: 26px; }
  .watermark { left: 40px; top: 300px; font-size: 78px; font-weight: 700; color: var(--faint); white-space: nowrap; }
  .contact { left: 301px; top: 29px; border-left: 1px solid #8b9bb0; height: 96px; padding-left: 6px; font-size: 6.4px; color: var(--grey-text); line-height: 1.4; }
  .contact-row { display: flex; align-items: center; gap: 3px; height: 12.6px; }
  .contact-name { font-size: 10px; font-weight: 700; color: var(--green-dark); }
  .icon { width: 10px; height: 10px; flex: none; }
  .address-lines { padding-left: 14px; margin-top: -2px; margin-bottom: 4px; }
  .footer-logo { left: 49px; top: 553px; font-size: 12px; display: flex; align-items: center; gap: 4px; }
  .footer-logo .brand-mark { width: 12px; height: 12px; }
  .footer-rule { width: 1px; height: 22px; background: #777; top: 558px; }
  .footer-text { font-size: 5.6px; color: var(--grey-text); line-height: 1.45; }
  .sender { left: 27px; top: 25px; font-size: 5.8px; color: var(--grey-text); line-height: 1.5; }
  .sender .contact-name { font-size: 10px; display: flex; align-items: center; gap: 4px; }
  .window { left: 28px; top: 130px; width: 180px; height: 72px; border: 1px solid #b8b8b8; border-radius: 9px; box-shadow: inset 2px 2px 4px rgba(0,0,0,0.18); box-sizing: border-box; }
  .recipient { left: 35px; top: 18px; font-size: 6.4px; color: #6d6d6d; line-height: 1.5; }
  .logo-envelope { left: 288px; top: 142px; font-size: 31px; display: flex; align-items: center; gap: 6px; }
  .logo-envelope .brand-mark { width: 22px; height: 22px; }
  .flap-name { font-size: 18px; font-weight: 700; color: var(--mark); white-space: nowrap; }
</style>
</head>
<body>
<div class="artboard">

  <!-- Letterhead -->
  <section class="sheet letterhead">
    <svg class="abs" style="left:0;top:0" width="420" height="595" viewBox="0 0 420 595">
      <polygon points="0,0 272,0 263,11 0,11" fill="var(--grey)"/>
      <polygon points="275,0 420,0 420,11 266,11" fill="var(--green)"/>
      <polygon points="3,584 275,584 266,595 3,595" fill="var(--green)"/>
      <polygon points="278,584 423,584 423,595 269,595" fill="var(--grey)"/>
    </svg>

    <div class="abs watermark">yourTidor</div>

    <div class="abs logo-main brand"><span class="brand-mark"></span>yourTidor</div>

    <div class="abs contact">
      <div class="contact-row contact-name">
        <svg class="icon" viewBox="0 0 10 10"><rect width="10" height="10" rx="2" fill="var(--green)"/><path d="M5 8.5 L2.6 4.6 A2.6 2.6 0 1 1 7.4 4.6 Z" fill="#fff"/><circle cx="5" cy="3.6" r="1" fill="var(--green)"/></svg>
        yourTidor
      </div>
      <div class="address-lines">Lindenweg 12<br>95100 Talheim</div>
      <div class="contact-row">
        <svg class="icon" viewBox="0 0 10 10"><rect width="10" height="10" rx="2" fill="var(--green)"/><path d="M2 4.2 Q5 2 8 4.2 L7.2 5 L6 4.4 L4 4.4 L2.8 5 Z M3.2 5.4 H6.8 V7.6 H3.2 Z" fill="#fff"/></svg>
        04127 / 31840 5
      </div>
      <div class="contact-row">
        <svg class="icon" viewBox="0 0 10 10"><rect width="10" height="10" rx="2" fill="var(--green)"/><rect x="2.5" y="2.2" width="5" height="5.6" fill="none" stroke="#fff" stroke-width="0.8"/><path d="M3.5 4 H6.5 M3.5 5.2 H6.5 M3.5 6.4 H6.5" stroke="#fff" stroke-width="0.5"/></svg>
        04127 / 31840 / 6 7
      </div>
      <div class="contact-row">
        <svg class="icon" viewBox="0 0 10 10"><rect width="10" height="10" rx="2" fill="var(--green)"/><text x="5" y="7.6" text-anchor="middle" font-size="8" font-family="Source Sans 3, sans-serif" fill="#fff">@</text></svg>
        info@tidor-mail.de
      </div>
      <div class="contact-row">
        <svg class="icon" viewBox="0 0 10 10"><rect width="10" height="10" rx="2" fill="var(--green)"/><circle cx="5" cy="5" r="2.8" fill="none" stroke="#fff" stroke-width="0.7"/><path d="M2.2 5 H7.8 M5 2.2 V7.8" stroke="#fff" stroke-width="0.5"/><ellipse cx="5" cy="5" rx="1.2" ry="2.8" fill="none" stroke="#fff" stroke-width="0.5"/></svg>
        www.tidor-ordnung.de
      </div>
    </div>

    <div class="abs footer-logo brand"><span class="brand-mark"></span>yourTidor</div>
    <div class="abs footer-rule" style="left:137px"></div>
    <div class="abs footer-text" style="left:174px;top:559px">Kreisbank Talheim<br>BLZ 000 400 00<br>Kto 300000000</div>
    <div class="abs footer-rule" style="left:270px"></div>
    <div class="abs footer-text" style="left:311px;top:563px">IBAN: DE00123400005678901234<br>BIC: KRBKDE1TXXX</div>
  </section>

  <!-- Envelope, front with open flap -->
  <svg class="abs" style="left:653px;top:183px" width="452" height="72" viewBox="0 0 452 72">
    <path d="M0 71 L22 7 Q24 1 30 1 L420 1 Q426 1 428 7 L450 71 Z" fill="var(--paper)" stroke="#c4c4c4" stroke-width="1"/>
  </svg>
  <div class="abs flap-name" style="left:838px;top:207px;transform:rotate(180deg)">yourTidor</div>

  <section class="sheet envelope-front">
    <div class="abs sender">
      <div class="contact-name brand">
        <svg class="icon" viewBox="0 0 10 10"><path d="M5 9.6 L1.6 4.4 A3.6 3.6 0 1 1 8.4 4.4 Z" fill="var(--mark)"/><circle cx="5" cy="3.6" r="1.4" fill="#fff"/></svg>
        yourTidor
      </div>
      <div style="padding-left:14px">Lindenweg 12<br>95100 Talheim</div>
    </div>
    <div class="abs window">
      <div class="abs recipient">Marta Kessler<br>Am Mühlbach 8<br>53700 Birkenau<br>SCHWEIZ</div>
    </div>
    <div class="abs logo-envelope brand"><span class="brand-mark"></span>yourTidor</div>
    <svg class="abs" style="left:0;top:223px" width="450" height="8" viewBox="0 0 450 8">
      <polygon points="0,0 298,0 291,8 0,8" fill="var(--grey)"/>
      <polygon points="301,0 450,0 450,8 294,8" fill="var(--green)"/>
    </svg>
  </section>

  <!-- Envelope, back with closed flap -->
  <section class="sheet envelope-back">
    <svg class="abs" style="left:0;top:0" width="450" height="72" viewBox="0 0 450 72">
      <path d="M0 0 L22 64 Q24 71 30 71 L420 71 Q426 71 428 64 L450 0" fill="var(--paper)" stroke="#c4c4c4" stroke-width="1" filter="drop-shadow(0 1px 1px rgba(0,0,0,0.15))"/>
    </svg>
    <div class="abs flap-name" style="left:185px;top:20px">yourTidor</div>
  </section>

  <!-- Trim guides -->
  <svg class="guides" width="1200" height="1000" viewBox="0 0 1200 1000">
    <g stroke="#555" stroke-width="0.6">
      <line x1="96" y1="165" x2="96" y2="190"/><line x1="516" y1="165" x2="516" y2="190"/>
      <line x1="96" y1="810" x2="96" y2="835"/><line x1="516" y1="810" x2="516" y2="835"/>
      <line x1="58" y1="202" x2="83" y2="202"/><line x1="529" y1="202" x2="554" y2="202"/>
      <line x1="58" y1="797" x2="83" y2="797"/><line x1="529" y1="797" x2="554" y2="797"/>
      <line x1="88" y1="406" x2="110" y2="406"/><line x1="88" y1="595" x2="110" y2="595"/>
      <line x1="653" y1="216" x2="653" y2="242"/><line x1="1103" y1="216" x2="1103" y2="242"/>
      <line x1="653" y1="497" x2="653" y2="522"/><line x1="1103" y1="497" x2="1103" y2="522"/>
      <line x1="653" y1="528" x2="653" y2="553"/><line x1="1103" y1="528" x2="1103" y2="553"/>
      <line x1="653" y1="810" x2="653" y2="835"/><line x1="1103" y1="810" x2="1103" y2="835"/>
      <line x1="615" y1="485" x2="640" y2="485"/><line x1="1116" y1="485" x2="1141" y2="485"/>
      <line x1="615" y1="797" x2="640" y2="797"/><line x1="1116" y1="797" x2="1141" y2="797"/>
      <g stroke-dasharray="4 5">
        <line x1="615" y1="254" x2="640" y2="254"/><line x1="1116" y1="254" x2="1141" y2="254"/>
        <line x1="615" y1="566" x2="640" y2="566"/><line x1="1116" y1="566" x2="1141" y2="566"/>
      </g>
    </g>
  </svg>

</div>
</body>
</html>
```